Stationary design for boutique production house

We need a stationary design for our production house, 'Lorno Productions' based in Singapore. We produce microfilms as well as podcasts, talkshows and events. Our logo is a stylized icon of our director, who is also the executive producer and host of our programs, Lorno. Our main company colors are Red, Black and white. We would like a clean, minimalist design incorporating our existing company logo that conveys a sense of urbanism and elegance.

Logo and font files are attached. f

Target Market(s)

We focus on lifestyle media rather than entertainment.

Industry/Entity Type

Boutique

Font styles to use
Serif
Sans Serif

Colors
ec1f27
ffffff
000000

Requirements
Must have
• Our company logo and at least one of our company colors.
Nice to have
• Our address and contact information.
Should not have
• Changes made to the company logo (using only certain parts of it is fine though)

```html
<!DOCTYPE html>
<html lang="en">
<head>
<meta charset="utf-8">
<title>Lorno Productions — Business Card</title>
<link rel="stylesheet" href="https://fonts.googleapis.com/css2?family=Noto+Serif:wght@400;700&display=swap">
<style>
  :root {
    --backdrop: #4a4a4a;
    --card-dark: #221f20;
    --card-light: #fafafa;
    --brand-red: #ec1f27;
    --ink: #1a1a1a;
    --paper-text: #ffffff;
  }
  * { margin: 0; padding: 0; box-sizing: border-box; }
  html, body {
    width: 1200px; height: 750px; overflow: hidden;
    background: var(--backdrop);
    font-family: "Noto Serif", Georgia, serif;
  }
  .stage { position: relative; width: 1200px; height: 750px; }
  .card {
    position: absolute; top: 228px;
    width: 461px; height: 263px; overflow: hidden;
  }
  .card--front { left: 124px; background: var(--card-dark); color: var(--paper-text); }
  .card--back { left: 595px; background: var(--card-light); }

  .holder { position: absolute; left: 37px; top: 42px; }
  .holder__name {
    color: var(--brand-red); font-weight: 700; font-size: 16px;
    letter-spacing: 0.3px; line-height: 1.2;
  }
  .holder__role { font-size: 12.5px; margin-top: 2px; }

  .address { position: absolute; left: 37px; top: 99px; font-size: 11.5px; line-height: 16px; font-style: normal; }

  .contacts { position: absolute; left: 37px; top: 139px; list-style: none; }
  .contacts li {
    display: flex; align-items: center; height: 18.5px;
    font-size: 11.5px;
  }
  .contacts svg { width: 12px; height: 12px; margin-right: 9px; fill: var(--brand-red); flex: none; }

  .edge-name {
    position: absolute; top: 0; height: 263px;
    display: flex; align-items: center; justify-content: center;
    writing-mode: vertical-rl;
    font-size: 62px; font-weight: 700; letter-spacing: 4px; line-height: 1;
  }
  .edge-name--front { right: 14px; color: var(--paper-text); transform: rotate(180deg); }
  .edge-name--back { left: 14px; color: var(--ink); }

  .seam-dot {
    position: absolute; left: 569px; top: 413px;
    width: 42px; height: 42px; border-radius: 50%;
    background: var(--brand-red);
  }

  .brand {
    position: absolute; left: 161px; width: 280px; top: 118px;
    display: flex; align-items: center; justify-content: center; gap: 9px;
  }
  .brand__dot { width: 11px; height: 11px; border-radius: 50%; background: var(--brand-red); flex: none; }
  .brand__name { font-size: 16px; font-weight: 400; color: var(--ink); letter-spacing: 0.5px; white-space: nowrap; }
</style>
</head>
<body>
<main class="stage">
  <section class="card card--front">
    <div class="holder">
      <p class="holder__name">MARA ELLISON</p>
      <p class="holder__role">CEO/Founder</p>
    </div>
    <address class="address">214 Tanjong Row<br>Singapore 088452</address>
    <ul class="contacts">
      <li><svg viewBox="0 0 12 12"><path d="M2.5 0.8l2 2-1 1.4c.6 1.5 1.8 2.7 3.3 3.3l1.4-1 2 2-1.2 1.9C5.9 10.2 1.8 6.1 0.6 2z"/></svg>6512 3408</li>
      <li><svg viewBox="0 0 12 12"><path d="M3 0h6v12H3zM4.2 1.4v7.8h3.6V1.4zM5.4 10h1.2v1H5.4z" fill-rule="evenodd"/></svg>9187 2265</li>
      <li><svg viewBox="0 0 12 12"><path d="M3 0h6v4H3zM0 4.5h12V10H0zM3 8h6v4H3z"/></svg>6512 3409</li>
      <li><svg viewBox="0 0 12 12"><path d="M0 2.5h12v1L6 7 0 3.5zM0 4.7l6 3.5 6-3.5V10H0z"/></svg>hello@lornoprod.sg</li>
      <li><svg viewBox="0 0 12 12"><path d="M6 0a6 6 0 100 12A6 6 0 006 0zm-1 2c1 .5 1.5 1.5 1 2.5S4 5.5 4.5 7 3 8.5 2 7.5 1.5 3 5 2zm3 5c1 0 2 .5 1.5 2S7 10.5 7 9.5 7 7 8 7z"/></svg>www.lornoprod.sg</li>
    </ul>
    <span class="edge-name edge-name--front">LORNO</span>
  </section>

  <section class="card card--back">
    <span class="edge-name edge-name--back">LORNO</span>
    <div class="brand">
      <span class="brand__dot"></span>
      <span class="brand__name">LORNO PRODUCTIONS</span>
    </div>
  </section>

  <span class="seam-dot"></span>
</main>
</body>
</html>
```